Business card design for Automotive workshop

We need a business card for a new automotive repair and tyre shop called Keelstone Prime Automotive located in New Zealand. We are a clean, modern and fresh workshop and company.

Front needs to feature logo,
my name:
Marlo Fenwicke (director)

Address:
48 Tarn Lane
Harrowby Bay 3587

Phone: 07 594 2713
Mobile: 027 451 9362
Email: office@keelstoneautomotive.example.nz
Website: keelstoneautomotive.example.nz

Back needs to feature an area to write down appointment details, date and time.

Also feature a list of jobs and work we do such as,
Vehicle Servicing
All Mechanical Repairs
Warrant of Fitness
Tyres & Wheel Alignments
Automotive Diagnostics
Automotive Parts & Supplies

```html
<!DOCTYPE html>
<html lang="en">
<head>
<meta charset="utf-8">
<title>Keelstone Prime Automotive – Business Card</title>
<link href="https://fonts.googleapis.com/css2?family=Open+Sans:wght@400;600;700&display=swap" rel="stylesheet">
<style>
  :root {
    --backdrop: #3a3431;
    --card: #111111;
    --panel: #2e2e2e;
    --red: #e3101f;
    --white: #ffffff;
    --muted: #d9d9d9;
    --rule: #8a8a8a;
  }
  * { box-sizing: border-box; margin: 0; padding: 0; }
  html, body {
    width: 1200px; height: 716px; overflow: hidden;
    background: var(--backdrop);
    font-family: "Open Sans", Arial, sans-serif;
  }
  .canvas {
    position: relative; width: 1200px; height: 716px;
    display: flex; align-items: center; justify-content: center; gap: 40px;
  }
  .card {
    position: relative; width: 540px; height: 309px;
    background: var(--card); color: var(--white);
    box-shadow: 0 14px 30px rgba(0,0,0,.45);
    overflow: hidden;
  }

  /* Back side */
  .appointment {
    position: absolute; left: 36px; top: 30px; width: 468px; height: 128px;
    background: var(--panel);
  }
  .appointment__title {
    position: absolute; top: 14px; width: 100%; text-align: center;
    color: var(--red); font-weight: 600; font-size: 17px; letter-spacing: .3px;
  }
  .appointment__fields {
    position: absolute; left: 22px; right: 22px; bottom: 26px;
    display: flex; gap: 22px; font-size: 13px; font-weight: 600;
  }
  .field { flex: 1; display: flex; align-items: flex-end; gap: 6px; }
  .field__line { flex: 1; border-bottom: 1px dashed var(--muted); height: 1px; margin-bottom: 4px; }

  .works { position: absolute; left: 36px; right: 36px; top: 180px; }
  .works__heading {
    display: flex; align-items: center; gap: 14px; justify-content: center;
    font-weight: 700; font-size: 13px; margin-bottom: 14px;
  }
  .works__heading::before, .works__heading::after {
    content: ""; width: 80px; height: 1px; background: var(--red);
  }
  .works__list {
    list-style: none; display: flex; flex-wrap: wrap; justify-content: center;
    gap: 8px 16px; font-size: 11.5px;
  }
  .works__list li::before {
    content: ""; display: inline-block; width: 5px; height: 5px; border-radius: 50%;
    background: var(--red); margin-right: 6px; vertical-align: middle;
  }

  /* Front side */
  .brand {
    position: absolute; left: 28px; top: 112px; width: 210px;
    font-weight: 700; font-size: 21px; line-height: 1.2; color: var(--white);
    letter-spacing: .5px; text-transform: uppercase;
  }
  .divider {
    position: absolute; left: 258px; top: 58px; width: 1px; height: 186px;
    background: var(--rule);
  }
  .contact { position: absolute; left: 282px; top: 52px; right: 18px; }
  .contact__name { color: var(--red); font-weight: 700; font-size: 20px; }
  .contact__role { font-size: 12px; margin: 2px 0 12px; }
  .contact__address { font-size: 12px; line-height: 1.45; margin-bottom: 10px; }
  .contact__list { list-style: none; font-size: 11.5px; line-height: 1.75; }
  .contact__list li { display: flex; align-items: center; gap: 7px; white-space: nowrap; }
  .contact__list svg { width: 10px; height: 10px; flex: none; }
  .accent-band {
    position: absolute; left: 0; right: 0; bottom: 0; height: 9px; background: var(--red);
  }
</style>
</head>
<body>
<main class="canvas">
  <section class="card card--back" aria-label="Card back">
    <div class="appointment">
      <h2 class="appointment__title">Appointment Details</h2>
      <div class="appointment__fields">
        <div class="field"><span>Date</span><span class="field__line"></span></div>
        <div class="field"><span>Time</span><span class="field__line"></span></div>
      </div>
    </div>
    <div class="works">
      <h3 class="works__heading">Our Works</h3>
      <ul class="works__list">
        <li>Vehicle Servicing</li>
        <li>Warrant of Fitness</li>
        <li>Automotive Parts &amp; Supplies</li>
        <li>Automotive Diagnostics</li>
        <li>Tyres &amp; Wheel Alignments</li>
        <li>All Mechanical Repairs</li>
      </ul>
    </div>
  </section>

  <section class="card card--front" aria-label="Card front">
    <div class="brand">Keelstone Prime Automotive</div>
    <div class="divider"></div>
    <div class="contact">
      <h1 class="contact__name">Marlo Fenwicke</h1>
      <p class="contact__role">Director</p>
      <p class="contact__address">48 Tarn Lane<br>Harrowby Bay 3587</p>
      <ul class="contact__list">
        <li><svg viewBox="0 0 10 10" aria-hidden="true"><path d="M2 1 L4 1 L4.6 3 L3.5 4 Q4.5 6 6 6.5 L7 5.4 L9 6 L9 8 Q5 9.5 1 3.5 Z" fill="#e3101f"/></svg>07 594 2713</li>
        <li><svg viewBox="0 0 10 10" aria-hidden="true"><rect x="2.5" y="0.5" width="5" height="9" rx="1" fill="none" stroke="#e3101f"/></svg>027 451 9362</li>
        <li><svg viewBox="0 0 10 10" aria-hidden="true"><rect x="0.5" y="2" width="9" height="6" fill="#e3101f"/><path d="M0.5 2 L5 5.5 L9.5 2" fill="none" stroke="#111"/></svg>office@keelstoneautomotive.example.nz</li>
        <li><svg viewBox="0 0 10 10" aria-hidden="true"><circle cx="5" cy="5" r="4.3" fill="none" stroke="#e3101f"/><path d="M0.7 5 H9.3 M5 0.7 Q2.5 5 5 9.3 M5 0.7 Q7.5 5 5 9.3" fill="none" stroke="#e3101f" stroke-width=".8"/></svg>keelstoneautomotive.example.nz</li>
      </ul>
    </div>
    <div class="accent-band"></div>
  </section>
</main>
</body>
</html>
```